Brightmill Data Works

Our company is about IT hardwares and IT solutions. IT hardware such as PC, RAMS, storage and servers. IT solutions such as project management, BA. We are also selling new technology too.

Target Market(s)

Consumer, Small to Medium Business, Corporate

Requirements
Must have
• The business card must have the following:
• Name:
• Title:
• Contact Number:
• Email address:
• Website:
• Color: Must match the logo color upgrade

```html
<!DOCTYPE html>
<html lang="en">
<head>
<meta charset="utf-8">
<title>Brightmill Data Works – Business Card</title>
<link href="https://fonts.googleapis.com/css2?family=Lato:wght@400;700;900&display=swap" rel="stylesheet">
<style>
  :root {
    --backdrop: #141414;
    --card: #1f1f1f;
    --card-deep: #181818;
    --orange: #e8962a;
    --white: #f4f4f4;
  }
  * { margin: 0; padding: 0; box-sizing: border-box; }
  html, body { width: 1200px; height: 912px; overflow: hidden; }
  body {
    background: var(--backdrop);
    font-family: "Lato", sans-serif;
    display: flex;
    flex-direction: column;
    align-items: center;
    justify-content: center;
    gap: 36px;
  }
  .card {
    width: 700px;
    height: 400px;
    position: relative;
    background: var(--card);
    box-shadow: 0 10px 30px rgba(0,0,0,.55);
    overflow: hidden;
  }
  /* Front */
  .card-front { background: var(--card-deep); }
  .front-texture {
    position: absolute; inset: 0;
    background: radial-gradient(ellipse at 60% 40%, #242424 0%, #151515 75%);
  }
  .front-content {
    position: absolute; inset: 0;
    display: flex; flex-direction: column;
    align-items: center; justify-content: center;
  }
  .brand {
    display: flex; flex-direction: column; align-items: center; gap: 16px;
  }
  .brand-mark {
    width: 30px; height: 30px;
    background: var(--orange);
  }
  .brand-name {
    font-weight: 900;
    color: var(--white);
    text-transform: uppercase;
    letter-spacing: 1px;
    font-size: 36px;
    line-height: 1;
    white-space: nowrap;
  }
  .front-web {
    margin-top: 30px;
    color: var(--white);
    font-size: 17px;
    letter-spacing: .5px;
  }
  /* Back */
  .back-brand {
    position: absolute;
    left: 0; top: 0; bottom: 0; width: 420px;
    padding: 0 30px;
    display: flex; align-items: center; justify-content: center;
  }
  .back-brand .brand { gap: 14px; }
  .back-brand .brand-name { font-size: 26px; }
  .back-brand .brand-mark { width: 24px; height: 24px; }
  .divider {
    position: absolute;
    left: 420px; top: 95px;
    width: 1.5px; height: 210px;
    background: var(--orange);
  }
  .contact {
    position: absolute;
    left: 455px; top: 92px;
    color: var(--white);
  }
  .person-name {
    color: var(--orange);
    font-weight: 700;
    font-size: 23px;
  }
  .person-title {
    font-size: 15px;
    margin-top: 2px;
  }
  .address {
    margin-top: 16px;
    font-size: 15px;
    line-height: 1.35;
  }
  .contact-list {
    list-style: none;
    margin-top: 14px;
    font-size: 15px;
  }
  .contact-list li {
    display: flex; align-items: center; gap: 10px;
    line-height: 1.45;
  }
  .contact-list svg { width: 13px; height: 13px; flex: none; fill: var(--orange); }
</style>
</head>
<body>

<section class="card card-front">
  <div class="front-texture" role="img" aria-label="Repeating pattern of the company symbol in faint dark grey"></div>
  <div class="front-content">
    <div class="brand">
      <span class="brand-mark"></span>
      <span class="brand-name">Brightmill Data Works</span>
    </div>
    <p class="front-web">www.brightmilldata.com</p>
  </div>
</section>

<section class="card card-back">
  <div class="back-brand">
    <div class="brand">
      <span class="brand-mark"></span>
      <span class="brand-name">Brightmill Data Works</span>
    </div>
  </div>
  <div class="divider"></div>
  <div class="contact">
    <p class="person-name">Daniel Ashford</p>
    <p class="person-title">Manager</p>
    <p class="address">418 Alder Row<br>Austin, TX 78702</p>
    <ul class="contact-list">
      <li>
        <svg viewBox="0 0 16 16" aria-hidden="true"><path d="M3.6 1 6 3.6 4.7 5.4c.8 2 2.2 3.5 4.2 4.3l1.7-1.4L15 10.6 13.3 14C7 14.3 1.6 8.8 2 2.6Z"/></svg>
        512 555 0142
      </li>
      <li>
        <svg viewBox="0 0 16 16" aria-hidden="true"><path d="M4 1h8v4H4Z M1 6h14v6h-3v3H4v-3H1Z M5.5 10v3.5h5V10Z"/></svg>
        512 555 0143
      </li>
      <li>
        <svg viewBox="0 0 16 16" aria-hidden="true"><path d="M1 3h14v1.2L8 9 1 4.2Z M1 5.8 8 10.6l7-4.8V13H1Z"/></svg>
        info@brightmilldata.com
      </li>
      <li>
        <svg viewBox="0 0 16 16" aria-hidden="true"><circle cx="8" cy="8" r="7"/><path d="M1 8h14M8 1c-3 3.5-3 10.5 0 14M8 1c3 3.5 3 10.5 0 14" stroke="#1f1f1f" stroke-width="1" fill="none"/></svg>
        www.brightmilldata.com
      </li>
    </ul>
  </div>
</section>

</body>
</html>
```